Business cards in digital learning for freelancer

Hello, I need a business cards in french. I work in the Digital learning industries as freeelancer; I'm an expert in digital learning. I work in France. My customer are in the health industry, pharmaceutical industry, and training organization. I've got a logo. I offer three services: consulting, Design, and Training. In the consulting, I offers coaching to choose your digital learning tools and the digital learning strategy. For the Design, I product differents level of elearning like rapid-learning, elearning, micro-learning, video-learning. And for the training service, I've create training about pedagogy, digital learning management project, Digital learning design.
I join my Logo create in this platform. My universe is gamified. I like the life, and I'm very social. I want a card like I'm I. I love Art (painting), Europeen comics. I use in my visual support "permanent maker" font and caracters. I would like cards: elegant, modern, Top class. If you need any information, you can ask me.
thanks for ideas

Target Market(s)

in health industries and training organization for Training manager, instructor, human resources director

Contact Information for Business Card

Phone number : 06 71 38 95 14 , mail: bastiengolmier@quelmoto.fr, web: bastiengolmier.fr , Carrivo

Font styles to use
Sans Serif

Requirements
Must have
• Use my logo and write my 3 services (consulting, training, design)

```html
<!DOCTYPE html>
<html lang="fr">
<head>
<meta charset="utf-8">
<title>Golmier Digital Learning – cartes de visite</title>
<link rel="stylesheet" href="https://fonts.googleapis.com/css2?family=Cinzel:wght@600&family=Questrial&display=swap">
<style>
  :root{
    --stage:#2e2e2e;
    --orange:#f07322;
    --orange-deep:#e0641a;
    --orange-soft:#f58a45;
    --paper:#ffffff;
    --grey:#6b6b6b;
    --grey-light:#c9c9c9;
    --mist:#efefef;
  }
  *{box-sizing:border-box;margin:0;padding:0}
  html,body{width:1200px;height:866px;overflow:hidden;background:var(--stage)}
  body{font-family:"Questrial",sans-serif;position:relative}

  .card{position:absolute;top:258px;width:540px;height:349px;overflow:hidden;box-shadow:0 10px 24px rgba(0,0,0,.45)}
  .card--front{left:40px;background:var(--paper)}
  .card--back{left:620px;background:var(--orange)}

  .watermark{position:absolute;border-radius:50%}
  .card--front .watermark{left:40px;top:-40px;width:330px;height:300px;
    background:radial-gradient(circle at 50% 50%,var(--mist) 0%,rgba(239,239,239,.6) 55%,rgba(255,255,255,0) 72%)}
  .card--back .watermark{left:110px;top:-30px;width:360px;height:380px;
    background:radial-gradient(circle at 50% 50%,var(--orange-deep) 0%,rgba(224,100,26,.5) 55%,rgba(240,115,34,0) 72%)}

  .holder{position:absolute;left:34px;top:74px}
  .holder__name{font-family:"Cinzel",serif;font-weight:600;color:var(--orange);font-size:22px;letter-spacing:1px}
  .holder__role{color:var(--grey);font-size:15px;margin-top:2px}
  .holder__rule{width:250px;height:1px;background:var(--grey-light);margin:6px 0 10px}
  .contact{display:flex;align-items:center;gap:8px;color:var(--grey);font-size:14px;line-height:22px}
  .contact svg{width:13px;height:13px;flex:none}

  .brand{position:absolute;text-align:center}
  .card--front .brand{right:36px;top:120px}
  .card--back .brand{left:0;right:0;top:120px}
  .brand__name{display:flex;align-items:center;justify-content:center;gap:10px;font-size:46px;letter-spacing:4px;line-height:1}
  .brand__dot{width:14px;height:14px;border-radius:50%;flex:none}
  .card--front .brand__name{color:var(--orange)}
  .card--front .brand__dot{background:var(--orange)}
  .card--back .brand__name{color:var(--paper)}
  .card--back .brand__dot{background:var(--paper)}
  .brand__tagline{font-family:"Cinzel",serif;font-weight:600;font-size:13px;letter-spacing:3px;margin-top:8px;display:flex;align-items:center;gap:8px;justify-content:center}
  .brand__tagline::before,.brand__tagline::after{content:"";height:1px;width:40px;background:currentColor}
  .card--front .brand__tagline{color:var(--grey)}
  .card--back .brand__tagline{color:var(--paper)}

  .services{position:absolute;left:0;right:0;top:214px;text-align:center;color:var(--paper);font-size:14px;letter-spacing:2px}

  .web{position:absolute;left:34px;right:34px;bottom:30px;display:flex;align-items:center;justify-content:flex-end;gap:14px}
  .web__rule{flex:1;height:1px;background:var(--grey-light)}
  .web__url{font-size:15px;color:var(--orange)}
  .web__url span{color:var(--grey)}
  .social{display:flex;align-items:center;gap:6px;color:var(--orange);font-size:13px}
  .social__dot{width:18px;height:18px;border-radius:50%;background:#0a72b5}
</style>
</head>
<body>

<section class="card card--front" aria-label="Recto de la carte">
  <div class="watermark" role="img" aria-label="Motif décoratif estompé de l'emblème de la marque"></div>

  <div class="holder">
    <h1 class="holder__name">Bastien Golmier</h1>
    <p class="holder__role">Managing Director</p>
    <div class="holder__rule"></div>
    <p class="contact">
      <svg viewBox="0 0 16 16" aria-hidden="true"><path fill="#f07322" d="M3.5 1.5l2.2 0.2 1 3-1.4 1.2c.8 1.8 2 3 3.8 3.8l1.2-1.4 3 1 .2 2.2c-.4 1-1.4 1.5-2.5 1.4C6 12.3 3.7 10 2.1 4c-.1-1.1.4-2.1 1.4-2.5z"/></svg>
      06 71 38 95 14
    </p>
    <p class="contact">
      <svg viewBox="0 0 16 16" aria-hidden="true"><rect x="1" y="3" width="14" height="10" fill="#f07322"/><path d="M1 3l7 6 7-6" fill="none" stroke="#fff" stroke-width="1.3"/></svg>
      bastiengolmier@quelmoto.fr
    </p>
  </div>

  <div class="brand">
    <div class="brand__name">GOLMIER<span class="brand__dot"></span></div>
    <div class="brand__tagline">Digital Learning</div>
  </div>

  <div class="web">
    <div class="web__rule"></div>
    <p class="web__url"><span>www.</span>bastiengolmier.fr</p>
    <p class="social"><span class="social__dot"></span>Carrivo</p>
  </div>
</section>

<section class="card card--back" aria-label="Verso de la carte">
  <div class="watermark" role="img" aria-label="Motif décoratif estompé de l'emblème de la marque"></div>
  <div class="brand">
    <div class="brand__name">GOLMIER<span class="brand__dot"></span></div>
    <div class="brand__tagline">Digital Learning</div>
  </div>
  <p class="services">CONSULTING • TRAINING • DESIGN</p>
</section>

</body>
</html>
```